we can communicate on this, but i want to follow the approach we took on Pellew|Marsh & Quinlan but i feel the card front needs the black background and the platinum and gold logo. The back? I am open. we can use the same info from PM&Q. Velmont Arc is an enhanced equity investment fund - basically a very exclusive boutique hedge fund that uses only stock options. very advanced things. hope you are interested

Contact Information for Business Card

Dr. Lewis T. Brennick, CFA
Scientifique de fusée financière
701.555.0143
LTBquant47@mailvantor.com

4718 Willow Creek Bend W.
West Fargo, ND 58078

No web site

Colors

Designer to choose colors to be used in the design.

Requirements
Nice to have
• I tend to prefer the most visible applications of the logo to include logo and name, the logo version with a black background and the gold and platinum components separated by the black. I see this working well for a single side (logo and name - this is card front to me).
• I am fairly open to other treatments on the reverse side with the data. To me, it makes sense to have a different color rendition of the logo on the reverse and it may be a muted black tone on tone or an oversized portion that would have spot UV. Or, the reverse may play with colors and layout
Should not have
• Other colors = no no
• Decorative font

```html
<!DOCTYPE html>
<html lang="en">
<head>
<meta charset="utf-8">
<title>Velmont Arc — Business Card</title>
<link rel="stylesheet" href="https://fonts.googleapis.com/css2?family=Jost:wght@300;400;600&display=swap">
<style>
  :root {
    --stage: #1b1b1b;
    --card: #141516;
    --platinum: #c9c9cb;
    --platinum-dim: #7d7e80;
    --gold: #d4ad3c;
    --white: #f2f2f2;
    --muted: #bfbfbf;
    --rule: #d9d9d9;
  }
  * { box-sizing: border-box; margin: 0; padding: 0; }
  html, body { width: 1200px; height: 800px; overflow: hidden; }
  body {
    background: var(--stage);
    font-family: "Jost", "Futura", sans-serif;
    display: flex;
    align-items: center;
    justify-content: center;
    gap: 40px;
  }
  .card {
    position: relative;
    width: 540px;
    height: 308px;
    background: var(--card);
    box-shadow: 0 10px 30px rgba(0,0,0,.45);
  }

  /* Front */
  .card-front .brand {
    position: absolute;
    inset: 0;
    display: flex;
    flex-direction: column;
    align-items: center;
    justify-content: center;
    gap: 18px;
  }
  .brand-mark {
    width: 96px; height: 96px;
    border-radius: 50%;
    background: var(--platinum-dim);
  }
  .brand-name {
    font-weight: 600;
    font-size: 34px;
    letter-spacing: 3px;
    color: var(--platinum);
    text-transform: uppercase;
  }

  /* Back */
  .holder {
    position: absolute;
    top: 26px; right: 30px;
    text-align: right;
  }
  .holder-name {
    font-weight: 600;
    font-size: 19px;
    color: var(--gold);
  }
  .holder-name small { font-size: 11px; }
  .holder-title {
    font-weight: 300;
    font-size: 10.5px;
    letter-spacing: .3px;
    color: var(--muted);
    text-transform: uppercase;
  }
  .back-brand {
    position: absolute;
    left: 38px; top: 112px;
    display: flex;
    flex-direction: column;
    align-items: flex-start;
    gap: 10px;
  }
  .back-brand .brand-mark {
    width: 64px; height: 64px;
    background: var(--gold);
  }
  .back-brand .brand-name {
    font-size: 22px;
    letter-spacing: 2px;
    color: var(--white);
  }
  .rule-long {
    position: absolute;
    left: 220px; right: 30px; top: 172px;
    border-top: 1px solid var(--rule);
  }
  .address {
    position: absolute;
    right: 30px; top: 184px;
    text-align: right;
    font-style: normal;
    font-weight: 300;
    font-size: 12.5px;
    line-height: 1.35;
    color: var(--muted);
  }
  .contacts {
    position: absolute;
    left: 38px; bottom: 32px;
    width: 230px;
    padding-top: 8px;
    border-top: 1px solid var(--rule);
    list-style: none;
    font-weight: 300;
    font-size: 12px;
    line-height: 1.5;
    color: var(--white);
  }
  .contacts li { display: flex; align-items: center; gap: 7px; }
  .contacts svg { width: 10px; height: 10px; flex: none; }
</style>
</head>
<body>

  <section class="card card-front" aria-label="Card front">
    <div class="brand">
      <span class="brand-mark"></span>
      <span class="brand-name">Velmont Arc</span>
    </div>
  </section>

  <section class="card card-back" aria-label="Card back">
    <div class="holder">
      <p class="holder-name">Dr. Lewis T. Brennick, <small>CFA</small></p>
      <p class="holder-title">Scientifique des fusées financières</p>
    </div>

    <div class="back-brand">
      <span class="brand-mark"></span>
      <span class="brand-name">Velmont Arc</span>
    </div>

    <div class="rule-long"></div>

    <address class="address">
      4718 Willow Creek Bend W.<br>
      West Fargo, ND 58078
    </address>

    <ul class="contacts">
      <li>
        <svg viewBox="0 0 10 10" aria-hidden="true"><rect x="2.5" y="0.5" width="5" height="9" rx="1" fill="none" stroke="var(--gold)" stroke-width="1"/></svg>
        701.555.0143
      </li>
      <li>
        <svg viewBox="0 0 10 10" aria-hidden="true"><rect x="0.5" y="2" width="9" height="6" fill="var(--gold)"/><path d="M0.5 2 L5 5.5 L9.5 2" fill="none" stroke="var(--card)" stroke-width="0.8"/></svg>
        LTBquant47@mailvantor.com
      </li>
    </ul>
  </section>

</body>
</html>
```